Velmora Freightway Solutions Business cards

Would like a very unique design catchy but professional for business cards. Please use log provided.Marlon WellsCeo and Founder TransCon Logistix Solutions1-888-913-3225mwells@tlsolutionsus.comwww.tlsolutionsus.com

```html
<!DOCTYPE html>
<html lang="en">
<head>
<meta charset="utf-8">
<title>Velmora Freightway Solutions – Business Cards</title>
<link href="https://fonts.googleapis.com/css2?family=Josefin+Sans:wght@600&family=Lato:wght@400;700&display=swap" rel="stylesheet">
<style>
  :root{
    --blue:#1290cf;
    --blue-deep:#0b6fae;
    --blue-light:#22a8de;
    --red:#d42030;
    --white:#ffffff;
    --paper:#f3f3f3;
    --backdrop:#e9e6e1;
  }
  html,body{margin:0;padding:0;overflow:hidden;}
  body{width:1200px;height:780px;background:var(--backdrop);position:relative;font-family:"Lato",sans-serif;}
  .card{position:absolute;width:540px;height:310px;border-radius:14px;overflow:hidden;background:var(--paper);box-shadow:0 10px 24px rgba(0,0,0,.18);}
  .card--front{left:30px;top:235px;}
  .card--back{left:630px;top:235px;}
  .card__shapes{position:absolute;inset:0;}
  .brand{position:absolute;display:flex;align-items:center;gap:10px;font-family:"Josefin Sans",sans-serif;font-weight:600;color:var(--blue);text-transform:uppercase;letter-spacing:1.5px;}
  .brand__mark{width:14px;height:14px;background:var(--blue);}
  .card--front .brand{left:40px;top:62px;font-size:19px;width:300px;line-height:1.25;}
  .card--back .brand{left:150px;top:70px;font-size:21px;width:300px;line-height:1.25;}
  .person{position:absolute;left:205px;top:180px;color:var(--white);text-align:right;width:128px;}
  .person__name{font-size:19px;font-weight:700;margin:0;}
  .person__role{font-size:12px;margin:2px 0 0;}
  .divider{position:absolute;left:343px;top:160px;width:1px;height:72px;background:rgba(255,255,255,.7);}
  .contact{position:absolute;left:354px;top:160px;list-style:none;margin:0;padding:0;color:var(--white);font-size:11.5px;}
  .contact li{display:flex;align-items:center;gap:7px;height:24px;}
  .contact svg{flex:none;}
  .band-text{position:absolute;left:0;right:0;bottom:0;height:40px;line-height:40px;text-align:center;color:var(--white);font-family:"Josefin Sans",sans-serif;font-weight:600;font-size:14px;letter-spacing:4px;text-transform:uppercase;}
  .web{position:absolute;left:40px;bottom:26px;color:var(--white);font-size:13px;letter-spacing:3px;}
</style>
</head>
<body>

<section class="card card--front">
  <svg class="card__shapes" viewBox="0 0 540 310" width="540" height="310" aria-hidden="true">
    <defs>
      <linearGradient id="frontBlue" x1="0" y1="0" x2="1" y2="1">
        <stop offset="0" stop-color="var(--blue-light)"/>
        <stop offset="1" stop-color="var(--blue-deep)"/>
      </linearGradient>
    </defs>
    <path d="M0,222 C200,198 352,128 392,0 L540,0 L540,270 L0,270 Z" fill="url(#frontBlue)"/>
    <path d="M0,206 C190,184 334,116 372,0" fill="none" stroke="var(--red)" stroke-width="3"/>
    <rect x="0" y="270" width="540" height="40" fill="var(--red)"/>
  </svg>
  <div class="brand"><span class="brand__mark"></span><span>Velmora Freightway Solutions</span></div>
  <div class="person">
    <p class="person__name">Dorian Pike</p>
    <p class="person__role">Ceo and Founder</p>
  </div>
  <div class="divider"></div>
  <ul class="contact">
    <li>
      <svg width="14" height="14" viewBox="0 0 14 14"><circle cx="7" cy="7" r="6.5" fill="none" stroke="#fff"/><path d="M5 4h1.4l.6 1.6-.8.6a4 4 0 0 0 1.6 1.6l.6-.8 1.6.6V10A5 5 0 0 1 5 4z" fill="#fff"/></svg>
      <span>1-888-470-6158</span>
    </li>
    <li>
      <svg width="14" height="14" viewBox="0 0 14 14"><circle cx="7" cy="7" r="6.5" fill="none" stroke="#fff"/><rect x="4" y="5" width="6" height="4.2" fill="none" stroke="#fff"/><path d="M4 5l3 2.3L10 5" fill="none" stroke="#fff"/></svg>
      <span>dpike@vfwayroutes.com</span>
    </li>
    <li>
      <svg width="14" height="14" viewBox="0 0 14 14"><circle cx="7" cy="7" r="6.5" fill="none" stroke="#fff"/><circle cx="7" cy="7" r="3.3" fill="none" stroke="#fff"/><path d="M3.7 7h6.6M7 3.7v6.6" stroke="#fff"/></svg>
      <span>www.vfwayroutes.com</span>
    </li>
  </ul>
  <div class="band-text">Velmora Freightway Solutions</div>
</section>

<section class="card card--back">
  <svg class="card__shapes" viewBox="0 0 540 310" width="540" height="310" aria-hidden="true">
    <defs>
      <linearGradient id="backBlue" x1="0" y1="0" x2="1" y2="0">
        <stop offset="0" stop-color="var(--blue-deep)"/>
        <stop offset="1" stop-color="var(--blue-light)"/>
      </linearGradient>
    </defs>
    <path d="M0,150 C110,240 300,270 540,276 L540,310 L0,310 Z" fill="url(#backBlue)"/>
    <path d="M0,134 C118,226 306,256 540,262" fill="none" stroke="var(--red)" stroke-width="3"/>
  </svg>
  <div class="brand"><span class="brand__mark"></span><span>Velmora Freightway Solutions</span></div>
  <div class="web">www.vfwayroutes.com</div>
</section>

</body>
</html>
```